TalkHarbor - Language Coaching Services

Sleek, innovative, trendy design for Language Coaching business.

TalkHarbor is a new UK based company that provides Language Coaching services. We offer highly personalized on-line and face to face language courses. We also impart learning techniques workshops based on the latest neuroscience research for second-language acquisition.

Target Market(s)

See attached info

Industry/Entity Type

Consulting

Contact Information for Business Card

TalkHarbor
DaniaKV@talkharbor.co.uk
TalkHarbor.co.uk
London, UK

Font styles to use
Sans Serif

```html
<!DOCTYPE html>
<html lang="en">
<head>
<meta charset="utf-8">
<title>TalkHarbor – Business Card</title>
<link rel="stylesheet" href="https://fonts.googleapis.com/css2?family=Montserrat:wght@500;600&family=Arimo:wght@400;700&display=swap">
<style>
  :root {
    --stage: #2c2d2f;
    --brand-blue: #1b6a8f;
    --brand-blue-deep: #15587a;
    --card-white: #f7f8f9;
    --ink: #1d1d1f;
    --ink-soft: #3a3a3c;
    --rule: #2a2a2a;
  }
  * { box-sizing: border-box; margin: 0; padding: 0; }
  html, body {
    width: 1200px; height: 997px; overflow: hidden;
    background: var(--stage);
  }
  .stage { position: relative; width: 1200px; height: 997px; }

  .card {
    position: absolute; width: 520px; height: 297px;
    overflow: hidden;
    box-shadow: 0 14px 30px rgba(0,0,0,.45);
  }

  /* Back of card */
  .card--back {
    left: 70px; top: 170px;
    background: var(--brand-blue);
    display: flex; align-items: center; justify-content: center; gap: 18px;
  }
  .back-ring {
    width: 150px; height: 150px; border-radius: 50%;
    border: 12px solid #ffffff;
  }
  .back-name {
    font-family: "Montserrat", sans-serif; font-weight: 500;
    font-size: 40px; color: #ffffff; letter-spacing: .5px;
  }

  /* Front of card */
  .card--front { left: 610px; top: 440px; background: var(--card-white); }
  .front-shapes { position: absolute; inset: 0; }

  .brand-mark {
    position: absolute; left: 196px; top: 18px;
    width: 64px; height: 64px; border-radius: 50%;
    border: 5px solid var(--brand-blue);
  }
  .brand-rule {
    position: absolute; left: 272px; top: 64px;
    width: 222px; height: 1px; background: var(--rule);
  }
  .brand-name {
    position: absolute; left: 130px; top: 86px;
    font-family: "Montserrat", sans-serif; font-weight: 500;
    font-size: 40px; color: var(--brand-blue); letter-spacing: .5px;
  }

  .person { position: absolute; left: 22px; top: 160px; font-family: "Arimo", sans-serif; }
  .person-name {
    font-size: 15px; font-weight: 700; color: var(--brand-blue-deep);
    letter-spacing: .3px; text-transform: uppercase;
  }
  .person-role { font-size: 13px; color: var(--ink); margin-top: 1px; }
  .person-rule {
    position: absolute; left: 190px; top: 170px;
    width: 140px; height: 1px; background: var(--rule);
  }

  .contact-list {
    position: absolute; left: 22px; top: 208px; list-style: none;
    font-family: "Arimo", sans-serif; font-size: 13px; color: var(--ink-soft);
  }
  .contact-list li { display: flex; align-items: center; gap: 8px; height: 19px; }
  .contact-icon { width: 14px; height: 14px; flex: none; }

  .address {
    position: absolute; right: 22px; top: 160px; text-align: right;
    font-family: "Arimo", sans-serif; font-size: 12px; line-height: 15px;
    color: var(--brand-blue-deep);
  }
  .website {
    position: absolute; right: 22px; top: 214px;
    font-family: "Arimo", sans-serif; font-size: 14px; font-weight: 700;
    color: #ffffff;
  }
</style>
</head>
<body>
<main class="stage">

  <section class="card card--back" aria-label="Business card, back">
    <span class="back-ring" aria-hidden="true"></span>
    <span class="back-name">TalkHarbor</span>
  </section>

  <section class="card card--front" aria-label="Business card, front">
    <svg class="front-shapes" width="520" height="297" viewBox="0 0 520 297" aria-hidden="true">
      <path d="M0 297 L0 280 L300 280 Q318 280 322 262 L330 226 Q334 208 352 208 L520 208 L520 297 Z" fill="var(--brand-blue)"/>
      <path d="M0 278 L0 270 L296 270 Q306 270 308 262 L310 256 L316 256 L313 266 Q310 278 298 278 Z" fill="#111"/>
    </svg>

    <span class="brand-mark" aria-hidden="true"></span>
    <span class="brand-rule" aria-hidden="true"></span>
    <div class="brand-name">TalkHarbor</div>

    <div class="person">
      <div class="person-name">Dania Kovell</div>
      <div class="person-role">Director</div>
    </div>
    <span class="person-rule" aria-hidden="true"></span>

    <ul class="contact-list">
      <li>
        <svg class="contact-icon" viewBox="0 0 14 14" aria-hidden="true"><circle cx="7" cy="7" r="7" fill="var(--brand-blue)"/><path d="M4 5 Q4 4 5 4 L9 4 Q10 4 10 5 L10 6 L8.5 6 L8.5 5.3 L5.5 5.3 L5.5 6 L4 6 Z M4.5 7 L9.5 7 L10 10 L4 10 Z" fill="#fff"/></svg>
        020 7946 0812
      </li>
      <li>
        <svg class="contact-icon" viewBox="0 0 14 14" aria-hidden="true"><circle cx="7" cy="7" r="7" fill="var(--brand-blue)"/><rect x="5" y="3" width="4" height="8" rx="0.8" fill="none" stroke="#fff" stroke-width="1"/></svg>
        07700 900 315
      </li>
      <li>
        <svg class="contact-icon" viewBox="0 0 14 14" aria-hidden="true"><circle cx="7" cy="7" r="7" fill="var(--brand-blue)"/><rect x="3.5" y="4.5" width="7" height="5" fill="none" stroke="#fff" stroke-width="1"/><path d="M3.5 4.5 L7 7.3 L10.5 4.5" fill="none" stroke="#fff" stroke-width="1"/></svg>
        DaniaKV@talkharbor.co.uk
      </li>
    </ul>

    <div class="address">Suite 4.12 28 Harbour Lane<br>London, UK</div>
    <div class="website">TalkHarbor.co.uk</div>
  </section>

</main>
</body>
</html>
```